Maple Grove Schools | brand new stationery!

We need stationery design with our new logo! Our company updated it's name and image and we like to incorporate the new one on our stationery, business cards and email signature. We are looking for fresh, new ideas!
Industry: Childcare, Elementary and Middle School
Company Name: Maple Grove Schools
Tagline: Bright Futures Start Here
Main colors: Blue, white and a little yellow
Star shape is something new for us! Do you see a way to incorporate it as a design element?

```html
<!DOCTYPE html>
<html lang="en">
<head>
<meta charset="UTF-8">
<title>Maple Grove Schools – Business Card</title>
<link href="https://fonts.googleapis.com/css2?family=Montserrat:wght@400;500;600;700&family=Roboto:wght@400&display=swap" rel="stylesheet">
<style>
  :root {
    --bg: #1e1e1f;
    --card-dark: #231f20;
    --card-blue: #06196f;
    --white: #ffffff;
    --silver: #d9d9d9;
    --yellow: #f7b900;
    --muted: #e6e8f2;
  }
  * { margin: 0; padding: 0; box-sizing: border-box; }
  html, body { width: 1200px; height: 874px; overflow: hidden; }
  body {
    background: var(--bg);
    font-family: "Montserrat", sans-serif;
    position: relative;
  }
  .card {
    position: absolute;
    border-radius: 22px;
    box-shadow: 0 18px 40px rgba(0,0,0,.55);
  }
  .card--front {
    left: 70px; top: 287px;
    width: 525px; height: 300px;
    background: var(--card-dark);
    display: flex; align-items: center; justify-content: center;
  }
  .brand {
    display: flex; align-items: center; gap: 16px;
  }
  .brand__dot {
    width: 46px; height: 46px; border-radius: 50%;
    background: var(--card-blue);
    flex: none;
  }
  .brand__name {
    font-weight: 600;
    font-size: 38px;
    line-height: 1.05;
    color: var(--silver);
  }
  .card--back {
    left: 770px; top: 175px;
    width: 300px; height: 525px;
    background: var(--card-blue);
    color: var(--white);
    padding: 70px 36px 0;
    display: flex; flex-direction: column; align-items: center;
    text-align: center;
  }
  .card--back .brand { gap: 10px; margin-bottom: 30px; }
  .card--back .brand__dot { width: 30px; height: 30px; background: var(--yellow); }
  .card--back .brand__name { font-size: 22px; color: var(--white); text-align: left; }
  .person__name {
    font-weight: 500; font-size: 24px; letter-spacing: .5px;
  }
  .person__role {
    color: var(--yellow); font-size: 15px; margin-top: 4px;
  }
  .divider {
    width: 18px; height: 2px; background: var(--white);
    margin: 16px auto;
  }
  .address {
    font-family: "Roboto", sans-serif;
    font-size: 14px; line-height: 1.45; color: var(--muted);
  }
  .icons {
    display: flex; gap: 6px; margin: 18px 0 14px;
  }
  .icon {
    width: 22px; height: 22px; border-radius: 50%;
    background: var(--yellow);
    display: flex; align-items: center; justify-content: center;
  }
  .icon svg { width: 12px; height: 12px; }
  .contacts {
    list-style: none;
    font-family: "Roboto", sans-serif;
    font-size: 14px; line-height: 1.5; color: var(--muted);
  }
</style>
</head>
<body>
  <section class="card card--front">
    <div class="brand">
      <span class="brand__dot"></span>
      <span class="brand__name">Maple Grove<br>Schools</span>
    </div>
  </section>

  <section class="card card--back">
    <div class="brand">
      <span class="brand__dot"></span>
      <span class="brand__name">Maple Grove<br>Schools</span>
    </div>
    <h1 class="person__name">DANIEL HARPER</h1>
    <p class="person__role">President</p>
    <div class="divider"></div>
    <p class="address">4120 Willow Bend Road<br>Juneau, Alaska 34890</p>
    <div class="icons">
      <span class="icon" aria-label="phone">
        <svg viewBox="0 0 24 24"><path fill="#06196f" d="M6.6 10.8a15 15 0 0 0 6.6 6.6l2.2-2.2c.3-.3.7-.4 1-.2 1.1.4 2.3.6 3.6.6.6 0 1 .4 1 1V20c0 .6-.4 1-1 1C10.6 21 3 13.4 3 4c0-.6.4-1 1-1h3.5c.6 0 1 .4 1 1 0 1.3.2 2.5.6 3.6.1.3 0 .7-.2 1z"/></svg>
      </span>
      <span class="icon" aria-label="mobile">
        <svg viewBox="0 0 24 24"><rect x="7" y="2" width="10" height="20" rx="2" fill="#06196f"/><rect x="9" y="5" width="6" height="12" fill="#f7b900"/></svg>
      </span>
      <span class="icon" aria-label="fax">
        <svg viewBox="0 0 24 24"><rect x="7" y="3" width="10" height="6" fill="#06196f"/><rect x="3" y="9" width="18" height="9" rx="2" fill="#06196f"/><rect x="7" y="15" width="10" height="6" fill="#06196f" stroke="#f7b900"/></svg>
      </span>
      <span class="icon" aria-label="email">
        <svg viewBox="0 0 24 24"><rect x="3" y="6" width="18" height="12" fill="#06196f"/><path d="M3 6l9 7 9-7" fill="none" stroke="#f7b900" stroke-width="1.5"/></svg>
      </span>
      <span class="icon" aria-label="website">
        <svg viewBox="0 0 24 24"><circle cx="12" cy="12" r="8" fill="none" stroke="#06196f" stroke-width="2.5"/><path d="M4 12h16M12 4v16" stroke="#06196f" stroke-width="2"/></svg>
      </span>
    </div>
    <ul class="contacts">
      <li>369-555-0142</li>
      <li>369-555-0187</li>
      <li>369-555-0163</li>
      <li>info@maplegroveschools.com</li>
      <li>maplegroveschools.com</li>
    </ul>
  </section>
</body>
</html>
```